website design for M&T Electric

A portfolio website for a high end commercial and residential electrical contracting company. The current site mandtelectric.example does not represent the current direction but the images in the gallery give you an idea of the work we do. Current logo will be uploaded shortly but is black text on white background.
Target Market(s)
General Contractors, Residential Home Owners, clients intersted in Velmora home automation.
Industry/Entity Type
Electrician
Coding
Coded - Design and coding required
Number of Pages Required
2 page
Font styles to use
Sans Serif
Colors
Designer to choose colors to be used in the design.
Requirements
Must have
- Portfolio section highlighting different service areas and products (Velmora Housepilot, etc)

```html
<!DOCTYPE html>
<html lang="en">
<head>
<meta charset="utf-8">
<title>M&amp;T Electric</title>
<link href="https://fonts.googleapis.com/css2?family=Old+Standard+TT:wght@400;700&family=Open+Sans:wght@400;600;700&family=Kaushan+Script&display=swap" rel="stylesheet">
<style>
:root{
  --ink:#111;
  --black:#0a0a0a;
  --white:#fff;
  --paper:#f2f2f2;
  --charcoal:#343434;
  --text-grey:#666;
  --light-text:#d8d8d8;
  --pill:#bbb;
  --serif:'Old Standard TT', serif;
  --sans:'Open Sans', sans-serif;
  --script:'Kaushan Script', cursive;
}
*{box-sizing:border-box;margin:0;padding:0}
html,body{width:1200px;height:3364px;overflow:hidden;background:var(--white)}
body{position:relative;font-family:var(--sans);color:var(--ink)}
.abs{position:absolute}
.btn{position:absolute;display:flex;align-items:center;justify-content:center;gap:10px;border-radius:27px;font-family:var(--sans);font-size:17px;font-weight:600;letter-spacing:.5px;text-transform:uppercase}
.btn svg{width:14px;height:14px}
.btn--light{background:var(--white);color:var(--ink);border:3px solid var(--white);box-shadow:0 0 0 2px var(--black) inset}
.btn--dark{background:var(--black);color:var(--white);box-shadow:0 0 0 3px var(--white) inset,0 0 0 2px var(--black)}
.section-title{position:absolute;left:0;width:1200px;text-align:center;font-family:var(--serif);font-size:44px;font-weight:400;letter-spacing:1px;text-transform:uppercase}

/* header */
.header{left:0;top:0;width:1200px;height:126px;background:var(--white)}
.topbar{left:392px;top:0;width:808px;height:52px;background:var(--charcoal);border-bottom-left-radius:40px;color:var(--white);font-size:17px;font-weight:700}
.topbar .call{left:95px;top:11px;display:flex;align-items:center;gap:10px}
.topbar .call svg{width:28px;height:28px}
.search{left:452px;top:10px;width:280px;height:32px;background:var(--white);border:1px solid #999;font-size:14px;font-weight:400;color:#666;padding:6px 10px}
.search-btn{left:692px;top:10px;width:40px;height:32px;background:var(--white);display:flex;align-items:center;justify-content:center}
.brand{left:80px;top:42px;font-family:var(--serif);font-size:46px;color:var(--ink)}
.nav{left:520px;top:72px;display:flex;gap:38px;font-family:var(--serif);font-size:21px;color:#777}
.nav .active{color:var(--ink);border-bottom:2px solid var(--ink);padding-bottom:10px}

/* hero */
.hero{left:0;top:126px;width:1200px;height:574px;background:linear-gradient(100deg,#050403 0%,#1c130c 35%,#4a3220 60%,#2a1c12 80%,#0f0a06 100%)}
.hero-title{left:78px;top:145px;font-family:var(--script);font-size:68px;color:var(--white)}
.hero-text{left:78px;top:250px;font-size:24px;font-weight:700;line-height:28px;color:var(--white)}
.hero .btn{left:78px;top:373px;width:248px;height:56px}

/* welcome */
.welcome{left:0;top:700px;width:1200px;height:348px;background:var(--paper)}
.welcome h2{left:78px;top:48px;font-family:var(--serif);font-size:44px;font-weight:400;letter-spacing:.5px}
.welcome p{left:78px;top:114px;width:630px;font-size:14.5px;line-height:24px;color:var(--text-grey)}
.welcome .btn{left:78px;top:242px;width:174px;height:54px}
.bulbs{left:740px;top:40px;width:392px;height:258px;background:radial-gradient(ellipse at center,#ffffff 0%,#e2e2e2 55%,rgba(242,242,242,0) 75%)}

/* services */
.card{top:1189px;width:233px;height:370px;background:var(--black);color:var(--white);text-align:center}
.card-img{width:233px;height:191px}
.card h3{font-family:var(--serif);font-weight:400;font-size:21px;line-height:26px;margin:18px 8px 10px}
.card p{font-size:13.5px;line-height:24px;color:var(--light-text);padding:0 8px}
.card a{display:inline-block;color:var(--light-text);text-decoration:underline;font-size:13.5px;text-transform:uppercase;line-height:24px}

/* about */
.about{left:0;top:1610px;width:1200px;height:375px;background:var(--black);color:var(--white)}
.about-img{left:78px;top:41px;width:440px;height:291px;border:2px solid #777;background:linear-gradient(180deg,#7f8c99 0%,#a7adb2 45%,#8a7c66 70%,#6e6a64 100%)}
.about h2{left:558px;top:50px;font-family:var(--serif);font-weight:400;font-size:44px}
.about p{left:558px;top:118px;width:570px;font-size:14.5px;line-height:27px;color:var(--light-text)}
.about .btn{left:558px;top:268px;width:172px;height:54px}

/* gallery */
.filters{left:38px;top:2109px;width:1124px;height:44px}
.filters .rule{position:absolute;left:0;top:22px;width:1124px;height:1px;background:var(--pill)}
.pill{position:absolute;top:0;height:44px;background:var(--white);border:1.5px solid var(--pill);border-radius:22px;display:flex;align-items:center;justify-content:center;text-align:center;font-size:14px;line-height:15px;color:#777}
.pill.active{background:var(--black);color:var(--white);border-color:var(--black)}
.tile{position:absolute}
.tile-overlay{left:8px;top:14px;width:400px;height:180px;background:rgba(40,40,40,.7);color:var(--white);text-align:center;font-family:var(--serif);font-size:28px;padding-top:28px}
.tile-overlay svg{display:block;margin:12px auto 0}
.view-all{left:522px;top:2760px;width:152px;height:54px}

/* contact */
.contact{left:0;top:2867px;width:1200px;height:441px;background:var(--charcoal);color:var(--white)}
.contact .section-title{top:46px;color:var(--white)}
.contact-name{left:117px;top:153px;font-size:19px;font-weight:700;text-transform:uppercase}
.contact-line{left:117px;display:flex;align-items:center;gap:16px;font-size:16px;color:var(--white)}
.contact-line svg{width:20px;height:20px}
.contact-line.bold{font-weight:700}
.map{left:588px;top:143px;width:498px;height:247px;background:linear-gradient(135deg,#e9e6df 0%,#dfe8d8 50%,#e6e3dc 100%)}
.footer{left:0;top:3308px;width:1200px;height:56px;background:var(--black);color:var(--white);font-size:15px;display:flex;align-items:center;justify-content:center}
</style>
</head>
<body>

<header class="abs header">
  <div class="abs brand">M&amp;T Electric</div>
  <div class="abs topbar">
    <div class="abs call">Call us now
      <svg viewBox="0 0 28 28"><circle cx="14" cy="14" r="12.5" fill="none" stroke="#fff" stroke-width="2"/><path d="M10 8c1 0 2 2 2 3s-1 1.5-1 2 2 4 4 4 1-1 2-1 3 1 3 2-1 2-3 2c-4 0-9-5-9-9 0-2 1-3 2-3z" fill="#fff"/></svg>
      (208) 555-0134</div>
    <div class="abs search">Search here...</div>
    <div class="abs search-btn"><svg width="16" height="16" viewBox="0 0 16 16"><circle cx="6.5" cy="6.5" r="4.5" fill="none" stroke="#111" stroke-width="2.2"/><path d="M10 10l4.5 4.5" stroke="#111" stroke-width="2.5"/></svg></div>
  </div>
  <nav class="abs nav">
    <span class="active">Home</span><span>About</span><span>Specialty Services</span><span>Gallery</span><span>Contact</span>
  </nav>
</header>

<section class="abs hero" role="img" aria-label="Photo of wooden steps lit by small recessed step lights at night">
  <div class="abs hero-title">M&amp;T Electric</div>
  <div class="abs hero-text">We offer commercial,<br>residential, light industrial,<br>and agricultural services.</div>
  <div class="btn btn--light">Contact us now <svg viewBox="0 0 14 14"><path d="M2 2l5 5-5 5M7 2l5 5-5 5" fill="none" stroke="#111" stroke-width="2"/></svg></div>
</section>

<section class="abs welcome">
  <h2 class="abs">WELCOME TO M &amp; T ELECTRIC</h2>
  <p class="abs">Lorem Ipsum is simply dummy text of the printing and typesetting industry. Lorem Ipsum has been the industry's standard dummy text ever since the 1500s, when an unknown printer took a galley of type and scrambled it to make a type specimen book. It has survived not only five centuries, but also the leap into electronic typesetting...</p>
  <div class="btn btn--dark">Read more <svg viewBox="0 0 14 14"><path d="M2 2l5 5-5 5M7 2l5 5-5 5" fill="none" stroke="#fff" stroke-width="2"/></svg></div>
  <div class="abs bulbs" role="img" aria-label="Product photo of LED bulbs and a recessed downlight"></div>
</section>

<h2 class="section-title" style="top:1094px">Specialty Services</h2>

<article class="abs card" style="left:78px">
  <div class="card-img" role="img" aria-label="Photo of a wall-mounted lighting keypad" style="background:linear-gradient(135deg,#b08650,#6e4a25)"></div>
  <h3>Velmora Housepilot</h3>
  <p>We're proudly certified to install Velmora Housepilot systems. Housepilot...</p>
  <a>Read more</a>
</article>
<article class="abs card" style="left:348px">
  <div class="card-img" role="img" aria-label="Photo of a living room with motorized window shades" style="background:linear-gradient(180deg,#c9c4bb,#6d6257)"></div>
  <h3>Velmora Drapeline QS Motorized Shades</h3>
  <p>Velmora Shades allow you to automatically adjust...</p>
  <a>Read more</a>
</article>
<article class="abs card" style="left:619px">
  <div class="card-img" role="img" aria-label="Photo of a lobby with LED ceiling lighting" style="background:linear-gradient(180deg,#f3e2a8,#b98c3c 60%,#4a3517)"></div>
  <h3>LED Lighting</h3>
  <p>LED Lighting has rapidly become a functional and affordable option...</p>
  <a>Read more</a>
</article>
<article class="abs card" style="left:888px">
  <div class="card-img" role="img" aria-label="Photo of a home standby generator" style="background:linear-gradient(180deg,#ffffff,#d6d8da);border:1px solid #999"></div>
  <h3>Emergency<br>Generators</h3>
  <p>Never be without power again&ndash;protect yourself from...</p>
  <a>Read more</a>
</article>

<section class="abs about">
  <div class="abs about-img" role="img" aria-label="Photo of the company's office building"></div>
  <h2 class="abs">ABOUT US</h2>
  <p class="abs">M &amp; T Electric is a full service electrical contracting shop. We offer commercial, residential, light industrial, and agricultural services. We're Velmora Housepilot and Velmora Motorized Shades certified, as well as an authorized Powerhaven generator dealer. We've served the Alder Valley and Upper Ridge area for over 18 years.</p>
  <div class="btn btn--light">Read more <svg viewBox="0 0 14 14"><path d="M2 2l5 5-5 5M7 2l5 5-5 5" fill="none" stroke="#111" stroke-width="2"/></svg></div>
</section>

<h2 class="section-title" style="top:2030px">Gallery</h2>
<div class="abs filters">
  <div class="rule"></div>
  <div class="pill" style="left:33px;width:60px">All</div>
  <div class="pill" style="left:100px;width:130px">Commercial</div>
  <div class="pill active" style="left:238px;width:124px">Residential</div>
  <div class="pill" style="left:382px;width:116px">Landscape</div>
  <div class="pill" style="left:506px;width:130px">Velmora<br>Housepilot</div>
  <div class="pill" style="left:644px;width:156px">Velmora Drapeline<br>Motorized Shades</div>
  <div class="pill" style="left:810px;width:100px">LED<br>Lighting</div>
  <div class="pill" style="left:918px;width:130px">Emergency<br>Generators</div>
</div>

<div class="tile" role="img" aria-label="Photo of a mountain home exterior in winter" style="left:0;top:2196px;width:415px;height:209px;background:linear-gradient(180deg,#8a8f94,#4a4640)">
  <div class="abs tile-overlay">Title
    <svg width="32" height="32" viewBox="0 0 32 32"><path d="M16 2v28M2 16h28" stroke="#fff" stroke-width="3"/></svg>
  </div>
</div>
<div class="tile" role="img" aria-label="Photo of a chandelier under a timber ceiling" style="left:0;top:2414px;width:415px;height:313px;background:radial-gradient(circle at 50% 45%,#e8b060,#6a3415 55%,#2a1408)"></div>
<div class="tile" role="img" aria-label="Photo of a lit commercial lobby with marble floors" style="left:426px;top:2196px;width:348px;height:531px;background:linear-gradient(180deg,#f4e6b8,#cbb077 45%,#8a7446 70%,#e6dcc4)"></div>
<div class="tile" role="img" aria-label="Photo of a large chandelier in a wood-beamed great room" style="left:783px;top:2196px;width:417px;height:312px;background:radial-gradient(circle at 50% 45%,#eab560,#72391a 55%,#2c150a)"></div>
<div class="tile" role="img" aria-label="Photo of a rustic kitchen with pendant lighting" style="left:783px;top:2519px;width:417px;height:208px;background:linear-gradient(180deg,#6a4426,#b08a64 55%,#3a2414)"></div>

<div class="btn btn--dark view-all">View all <svg viewBox="0 0 14 14"><path d="M2 2l5 5-5 5M7 2l5 5-5 5" fill="none" stroke="#fff" stroke-width="2"/></svg></div>

<section class="abs contact">
  <h2 class="section-title">Contact Us</h2>
  <div class="abs contact-name">M &amp; T Electric</div>
  <div class="abs contact-line" style="top:201px"><svg viewBox="0 0 20 20"><path d="M10 1a6 6 0 0 0-6 6c0 5 6 12 6 12s6-7 6-12a6 6 0 0 0-6-6zm0 8.5A2.5 2.5 0 1 1 10 4.5a2.5 2.5 0 0 1 0 5z" fill="#fff"/></svg>220 Fieldstone Way, PO Box 1180, Alder Falls, MT 59999</div>
  <div class="abs contact-line bold" style="top:242px"><svg viewBox="0 0 20 20"><path d="M5 2c1.5 0 3 3 3 4s-1.5 1.5-1.5 2.5 3 5 5 5 1.5-1.5 2.5-1.5 4 1.5 4 3-1.5 3-4 3C8 18 2 12 2 6c0-2.5 1.5-4 3-4z" fill="#fff"/></svg>(208) 555-0134</div>
  <div class="abs contact-line" style="top:282px"><svg viewBox="0 0 20 20"><rect x="2" y="4.5" width="16" height="11" fill="none" stroke="#fff" stroke-width="1.8"/><path d="M2 5l8 6 8-6" fill="none" stroke="#fff" stroke-width="1.8"/></svg>dmarsh@mandtelectric.example</div>
  <div class="abs contact-line" style="top:317px"><svg viewBox="0 0 20 20"><rect x="2" y="4.5" width="16" height="11" fill="none" stroke="#fff" stroke-width="1.8"/><path d="M2 5l8 6 8-6" fill="none" stroke="#fff" stroke-width="1.8"/></svg>tparker@mandtelectric.example</div>
  <div class="abs map" role="img" aria-label="Street map showing the office location"></div>
</section>

<footer class="abs footer">&copy;&nbsp;<b>M &amp; T Electric</b>&nbsp;- 2017. All Rights Reserved.</footer>

</body>
</html>
```